Hollendorf Business Card

This is the personal business card for Dr Mark Hollendorf and convers three area of his professional activity - all of them involve (foreign) languages:
o QRVB International Ltd - A translation company with 50 staff. Trades internationally
o WideHarbor Ltd - a global online auction marketplace for translation services (startup)
o Tonal Mosaic - cutting edge technology from the brain sciences which helps learners assimilate the sound patterns of a new language (startup)

Target Market(s)

The card needs to have a "cutting edge" feel - but for a fairly conservative audience - academics, investors.

Industry/Entity Type

Business

Requirements
Must have
• Text:
Dr Mark Hollendorf

Co-founder QRVB International Ltd (Language translation)
Founder WideHarbor Ltd (Translation marketplace)
Founder Tonal Mosaic (Language acquisition)

email: mark.oswin@velmora.co.nz
Phone: +64 21 596 3172
Chirpline: @MarkOswin7

```html
<!DOCTYPE html>
<html lang="en">
<head>
<meta charset="utf-8">
<title>Hollendorf Business Card</title>
<link rel="stylesheet" href="https://fonts.googleapis.com/css2?family=Michroma&family=Saira:wght@500;600;700&display=swap">
<style>
  :root {
    --backdrop: #4b4b4d;
    --card-white: #ffffff;
    --brand-blue: #4388c8;
    --ink: #1b1b1b;
    --on-blue: #ffffff;
  }
  * { margin: 0; padding: 0; box-sizing: border-box; }
  html, body {
    width: 1200px;
    height: 534px;
    overflow: hidden;
    background: var(--backdrop);
  }
  .stage {
    position: relative;
    width: 1200px;
    height: 534px;
  }
  .card {
    position: absolute;
    top: 119px;
    width: 517px;
    height: 295px;
    border-radius: 18px;
    overflow: hidden;
  }
  .card--front {
    left: 62px;
    background: var(--card-white);
  }
  .card--front .side-band {
    position: absolute;
    top: 0;
    right: 0;
    width: 114px;
    height: 100%;
    background: var(--brand-blue);
  }
  .card--back {
    left: 622px;
    background: var(--brand-blue);
  }
  .name {
    font-family: "Michroma", sans-serif;
    font-weight: 400;
    line-height: 1;
    white-space: nowrap;
  }
  .ventures {
    font-family: "Saira", sans-serif;
    font-weight: 700;
    font-size: 9.5px;
    line-height: 1;
    white-space: nowrap;
  }
  .ventures .divider { font-weight: 500; opacity: .55; padding: 0 4px; }

  .front-block {
    position: absolute;
    right: 143px;
    text-align: right;
    white-space: nowrap;
  }
  .front-block--identity { top: 38px; }
  .card--front .name {
    color: var(--brand-blue);
    font-size: 19px;
    letter-spacing: 0.6px;
  }
  .card--front .ventures { color: var(--ink); margin-top: 8px; }

  .contact, .roles {
    font-family: "Saira", sans-serif;
    font-size: 12px;
    font-weight: 600;
    line-height: 16px;
    color: var(--ink);
  }
  .front-block--contact { top: 161px; }
  .front-block--roles { top: 223px; }
  .label, .company { color: var(--brand-blue); font-weight: 500; }
  .note { font-size: 10.5px; }

  .back-identity {
    position: absolute;
    top: 124px;
    left: 0;
    width: 100%;
    text-align: center;
    color: var(--on-blue);
  }
  .card--back .name { font-size: 24px; letter-spacing: 1.2px; }
  .card--back .ventures { margin-top: 11px; }
</style>
</head>
<body>
<main class="stage">
  <section class="card card--front" aria-label="Card front">
    <div class="side-band"></div>
    <div class="front-block front-block--identity">
      <h1 class="name">DR MARK HOLLENDORF</h1>
      <p class="ventures">QRVB International Ltd<span class="divider">|</span>WideHarbor Ltd<span class="divider">|</span>Tonal Mosaic</p>
    </div>
    <div class="front-block front-block--contact contact">
      <p><span class="label">Email:</span> mark.oswin@velmora.co.nz</p>
      <p><span class="label">Phone:</span> +64 21 596 3172</p>
      <p><span class="label">Chirpline:</span> @MarkOswin7</p>
    </div>
    <div class="front-block front-block--roles roles">
      <p>Co-founder <span class="company">QRVB International Ltd</span> <span class="note">(Language translation)</span></p>
      <p>Founder <span class="company">WideHarbor Ltd</span> <span class="note">(Translation marketplace)</span></p>
      <p>Founder <span class="company">Tonal Mosaic</span> <span class="note">(Language acquisition)</span></p>
    </div>
  </section>

  <section class="card card--back" aria-label="Card back">
    <div class="back-identity">
      <h2 class="name">DR MARK HOLLENDORF</h2>
      <p class="ventures">QRVB International Ltd<span class="divider">|</span>WideHarbor Ltd<span class="divider">|</span>Tonal Mosaic</p>
    </div>
  </section>
</main>
</body>
</html>
```